Business Cards for new orthopaedic surgery practice

My husband and I are starting our own orthopaedic surgery practice. We are looking for a business card that is uniform, but one will have my name/title and the other will have his. You can just create one design with my name on it for now. But when I choose your design as the winning design I will ask that you add another copy with his name/title.

We are looking for classy, simple, elite all in one. We like dark blues/a little gold/yellow. Something that goes with our logo. We want our logo incorporated. Here is all the info you need:
Business name: RV Bone & Vitality Center
Location: 38517 North Willowmere Ave
Maple Hollow, FL 33408
Phone: 954-218-4063
Fax: 954-582-7341
Email: info@myrvbonecare.example

Names: Lydia Vance, M.D.
Board Certified Hand and Upper Extremity Surgeon

Ebo Dansu, M.D.
Board Certified Hip & Knee Replacement/General Orthopaedic Surgeon

Can decide what you want to put on the back. Maybe a slogan:
Grounded in Care. Centered on You

I am just going to upload our logo. The only thing is if we select you as the winning design, the location, and phone numbers may change. We will need your help to update that once fully solidified.

Industry/Entity Type

Medical

Contact Information for Business Card

Colors
0054AA
0677BA
7BADD7
CADEEF
E8F1F8
0094D4
00A9DD
6FCCEA
C7EBF8
E9F6FB

Requirements
Must have
• class, appeal,
Should not have
• We want to air on the side of masculine if we are looking at masculine vs. feminine feel. But we still want it classy, sophisticated, and something we will love

```html
<!DOCTYPE html>
<html lang="en">
<head>
<meta charset="utf-8">
<title>RV Bone &amp; Vitality Center – Business Card</title>
<link rel="stylesheet" href="https://fonts.googleapis.com/css2?family=Cinzel:wght@600;700&family=Arimo:wght@400&display=swap">
<style>
  :root {
    --canvas: #e4e4e4;
    --paper: #ffffff;
    --navy: #1f2d58;
    --navy-top: #283a66;
    --navy-bottom: #1b2953;
    --gold: #c4a15a;
    --ink: #3b3b3b;
    --rule: #d2d2d2;
  }
  * { margin: 0; padding: 0; box-sizing: border-box; }
  html, body { width: 1200px; height: 1200px; overflow: hidden; }
  body {
    background: var(--canvas);
    position: relative;
    font-family: "Arimo", Arial, sans-serif;
  }
  .card {
    position: absolute;
    left: 256px;
    width: 688px;
    height: 393px;
    overflow: hidden;
  }
  .card-front { top: 150px; background: var(--paper); }
  .card-back {
    top: 650px;
    background: linear-gradient(180deg, var(--navy-top), var(--navy-bottom));
  }

  /* front */
  .brand-front {
    position: absolute;
    left: 480px;
    top: 62px;
    width: 160px;
    text-align: center;
    font-family: "Cinzel", Georgia, serif;
    font-weight: 700;
    font-size: 19px;
    line-height: 1.35;
    color: var(--navy);
  }
  .doctor-name {
    position: absolute;
    left: 48px;
    top: 222px;
    font-family: "Cinzel", Georgia, serif;
    font-weight: 700;
    font-size: 24px;
    letter-spacing: 0.5px;
    color: var(--navy);
  }
  .doctor-title {
    position: absolute;
    left: 48px;
    top: 256px;
    font-size: 15.5px;
    color: var(--gold);
  }
  .divider {
    position: absolute;
    left: 48px;
    top: 281px;
    width: 592px;
    height: 1px;
    background: var(--rule);
  }
  .contact-list {
    position: absolute;
    left: 44px;
    top: 291px;
    list-style: none;
    font-size: 16px;
    line-height: 20.5px;
    color: var(--ink);
  }
  .contact-list li { display: flex; align-items: center; gap: 7px; }
  .contact-list svg { width: 14px; height: 14px; fill: var(--navy); flex: none; }
  .address {
    position: absolute;
    right: 44px;
    top: 292px;
    text-align: right;
    font-size: 16px;
    font-style: normal;
    line-height: 20.5px;
    color: var(--ink);
  }
  .band-navy {
    position: absolute; left: 0; bottom: 0;
    width: 419px; height: 16px; background: var(--navy);
  }
  .band-gold {
    position: absolute; left: 423px; bottom: 0;
    width: 265px; height: 16px; background: var(--gold);
  }

  /* back */
  .brand-back {
    position: absolute;
    left: 0;
    width: 100%;
    top: 148px;
    text-align: center;
    font-family: "Cinzel", Georgia, serif;
    font-weight: 700;
    font-size: 30px;
    line-height: 1.3;
    color: #ffffff;
  }
  .slogan {
    position: absolute;
    left: 0;
    width: 100%;
    top: 337px;
    text-align: center;
    font-size: 15.5px;
    letter-spacing: 3.4px;
    color: var(--gold);
  }
</style>
</head>
<body>

<section class="card card-front">
  <div class="brand-front">RV Bone &amp;<br>Vitality<br>Center</div>

  <h1 class="doctor-name">LYDIA VANCE, M.D.</h1>
  <p class="doctor-title">Board Certified Hand and Upper Extremity Surgeon</p>
  <div class="divider"></div>

  <ul class="contact-list">
    <li>
      <svg viewBox="0 0 24 24" aria-hidden="true"><path d="M6.6 10.8a15.1 15.1 0 0 0 6.6 6.6l2.2-2.2a1 1 0 0 1 1-.25 11.4 11.4 0 0 0 3.6.57 1 1 0 0 1 1 1V20a1 1 0 0 1-1 1A17 17 0 0 1 3 4a1 1 0 0 1 1-1h3.5a1 1 0 0 1 1 1c0 1.25.2 2.45.57 3.6a1 1 0 0 1-.25 1z"/></svg>
      954-218-4063
    </li>
    <li>
      <svg viewBox="0 0 24 24" aria-hidden="true"><path d="M6 2h9l3 3v4H6z M3 10h18v8h-3v4H6v-4H3z M8 16v4h8v-4z"/></svg>
      954-582-7341
    </li>
    <li>
      <svg viewBox="0 0 24 24" aria-hidden="true"><path d="M2 5h20v14H2z M4 7v.4l8 5.2 8-5.2V7z" fill-rule="evenodd"/></svg>
      info@myrvbonecare.example
    </li>
  </ul>

  <address class="address">
    38517 North Willowmere Ave<br>
    Maple Hollow, FL 33408<br>
    www.myrvbonecare.example
  </address>

  <div class="band-navy"></div>
  <div class="band-gold"></div>
</section>

<section class="card card-back">
  <div class="brand-back">RV Bone &amp;<br>Vitality Center</div>
  <p class="slogan">GROUNDED IN CARE. CENTERED ON YOU</p>
</section>

</body>
</html>
```